Tolvik Commercial Cleaning is lookong for a new business card design.

A fresh new design that's professional and stylish. We need a serious upgrade to our business cards. I have included pictures of our existing ones. Our clients include professional individuals and business owners. We woupdblike something professional and upbeat. Please have fun and see what you come uo with.

Target Market(s)

Property managers, business owners, facility managers and other similar professionals

Industry/Entity Type

Janitorial

Contact Information for Business Card

Name, cell, office number, email, web address

Font styles to use
Sans Serif

Colors

Designer to choose colors to be used in the design.

Requirements
Must have
• please use the green color in our logo
Nice to have
• Bar code
Should not have
• Address

```html
<!DOCTYPE html>
<html lang="en">
<head>
<meta charset="utf-8">
<title>Tolvik Commercial Cleaning – Business Card</title>
<link href="https://fonts.googleapis.com/css2?family=Arimo:wght@400;700&display=swap" rel="stylesheet">
<style>
  :root {
    --bg: #2a2a2a;
    --green: #3ab75a;
    --white: #ffffff;
    --ink: #3c3c3c;
    --blue: #2f5ea8;
  }
  * { margin: 0; padding: 0; box-sizing: border-box; }
  html, body {
    width: 1200px; height: 947px; overflow: hidden;
    background: var(--bg);
    font-family: "Arimo", Arial, sans-serif;
  }
  .stage { position: relative; width: 1200px; height: 947px; }
  .card {
    position: absolute;
    width: 540px; height: 310px;
    border-radius: 22px;
    overflow: hidden;
  }
  .card-front {
    left: 50px; top: 150px;
    background: var(--green);
    display: flex; flex-direction: column;
    align-items: center; justify-content: center;
    color: var(--white);
    font-weight: 700;
  }
  .front-name { font-size: 84px; line-height: 1; letter-spacing: 1px; }
  .front-sub { font-size: 24px; margin-top: 12px; letter-spacing: 1px; }

  .card-back {
    left: 610px; top: 480px;
    background: var(--white);
  }
  .back-brand {
    position: absolute; right: 32px; top: 30px;
    text-align: right; color: var(--green); font-weight: 700;
  }
  .back-brand .brand-main { font-size: 44px; line-height: 1; }
  .back-brand .brand-sub { font-size: 14px; margin-top: 6px; letter-spacing: .5px; }
  .person {
    position: absolute; left: 34px; top: 162px;
  }
  .person-name {
    color: var(--green); font-weight: 700; font-size: 26px; margin-bottom: 12px;
  }
  .contact-list { list-style: none; }
  .contact-list li {
    display: flex; align-items: center; gap: 10px;
    font-size: 16px; color: var(--ink); line-height: 1.45;
  }
  .contact-list svg { width: 14px; height: 14px; fill: var(--blue); flex: none; }
  .band {
    position: absolute; left: 0; right: 0; bottom: 0; height: 22px;
    background: var(--green);
  }
</style>
</head>
<body>
<main class="stage">
  <section class="card card-front">
    <div class="front-name">Tolvik</div>
    <div class="front-sub">Commercial Cleaning</div>
  </section>

  <section class="card card-back">
    <div class="back-brand">
      <div class="brand-main">Tolvik</div>
      <div class="brand-sub">Commercial Cleaning</div>
    </div>
    <div class="person">
      <div class="person-name">Marta Velling</div>
      <ul class="contact-list">
        <li>
          <svg viewBox="0 0 24 24" aria-hidden="true"><path d="M6.6 10.8a15.1 15.1 0 0 0 6.6 6.6l2.2-2.2a1 1 0 0 1 1-.25 11.4 11.4 0 0 0 3.6.57 1 1 0 0 1 1 1V20a1 1 0 0 1-1 1A17 17 0 0 1 3 4a1 1 0 0 1 1-1h3.5a1 1 0 0 1 1 1c0 1.25.2 2.45.57 3.6a1 1 0 0 1-.25 1z"/></svg>
          (555) 014-2290
        </li>
        <li>
          <svg viewBox="0 0 24 24" aria-hidden="true"><path d="M2 5h20v14H2z M3 6l9 7 9-7" fill="none" stroke="#2f5ea8" stroke-width="2"/></svg>
          marta@tolvikcleaning.com
        </li>
        <li>
          <svg viewBox="0 0 24 24" aria-hidden="true"><circle cx="12" cy="12" r="10"/><path d="M2 12h20M12 2c3 3 3 17 0 20M12 2c-3 3-3 17 0 20" fill="none" stroke="#ffffff" stroke-width="1.5"/></svg>
          www.tolvikcleaning.com
        </li>
      </ul>
    </div>
    <div class="band"></div>
  </section>
</main>
</body>
</html>
```